female esthetician looking for an impact business card

I an an expert in skin care industry with high experience in NYC.I want my business card to look professional , an impact at first look. I do want a combination between white and gold . I believe the font will be great if is gold.. The Fonts are also important. MIRABELA COSTINA (SKIN CARE BOUTIQUE)

THIS SHOULD BE THE BUSINESS NAME, and should be placed on th eback of the card.
IN front m, the name MIRABELA COSTINA - ESTHETCIAN

BY APPOINTMENTS ONLY: 518.240.7136

Target Market(s)

HIGH END CLIENTELE

Contact Information for Business Card

iT WILL BE on a luxury paper. I neeed the wow feeling

Requirements
Should not have
• pictures

```html
<!DOCTYPE html>
<html lang="en">
<head>
<meta charset="utf-8">
<title>Mirabela Costina – Skin Care Boutique Business Card</title>
<link href="https://fonts.googleapis.com/css2?family=Cinzel:wght@400;600&family=Lato:wght@300;400&display=swap" rel="stylesheet">
<style>
  :root {
    --backdrop: #26262a;
    --card: #ffffff;
    --card-edge: #ece7da;
    --gold: #c39a1f;
    --gold-deep: #a98113;
    --text-dark: #3a3a3a;
    --text-muted: #8a8170;
    --rule: #d9cfb4;
    --flourish: #f6f1e4;
  }
  * { box-sizing: border-box; margin: 0; padding: 0; }
  html, body { width: 1200px; height: 900px; overflow: hidden; }
  body {
    background: var(--backdrop);
    font-family: "Lato", sans-serif;
    position: relative;
  }
  .card {
    position: absolute;
    left: 320px;
    width: 560px;
    height: 320px;
    border-radius: 22px;
    background: var(--card);
    box-shadow: 0 18px 40px rgba(0,0,0,.5), inset 0 0 0 1px var(--card-edge);
    overflow: hidden;
  }
  .card--back { top: 100px; }
  .card--front { top: 480px; }

  .flourish {
    position: absolute;
    background: radial-gradient(ellipse at center, var(--flourish) 0%, rgba(246,241,228,0) 70%);
  }
  .card--back .flourish { inset: 0; }
  .card--front .flourish { left: 0; top: 0; width: 280px; height: 260px; }

  .brand-name {
    font-family: "Cinzel", serif;
    font-weight: 400;
    color: var(--gold);
    letter-spacing: 1px;
    white-space: nowrap;
  }
  .brand-tagline {
    font-family: "Lato", sans-serif;
    font-weight: 400;
    color: var(--text-muted);
    letter-spacing: 6px;
    text-transform: uppercase;
    white-space: nowrap;
  }

  .card--back .brand {
    position: absolute;
    left: 0; right: 0; top: 128px;
    text-align: center;
  }
  .card--back .brand-name { font-size: 36px; }
  .card--back .brand-tagline { font-size: 10px; margin-top: 6px; }

  .card--front .brand {
    position: absolute;
    right: 34px; top: 58px;
    text-align: right;
  }
  .card--front .brand-name { font-size: 32px; }
  .card--front .brand-tagline { font-size: 9px; margin-top: 4px; }

  .divider {
    position: absolute;
    left: 200px; right: 34px; top: 150px;
    height: 1px;
    background: var(--rule);
  }

  .person {
    position: absolute;
    left: 34px; top: 172px;
  }
  .person-name {
    font-family: "Cinzel", serif;
    font-weight: 600;
    font-size: 20px;
    color: var(--gold-deep);
    letter-spacing: .5px;
  }
  .person-role {
    font-size: 15px;
    color: var(--text-dark);
    margin-top: 1px;
  }
  .contact-list {
    list-style: none;
    margin-top: 12px;
  }
  .contact-list li {
    display: flex;
    align-items: center;
    gap: 8px;
    font-size: 15px;
    color: var(--text-dark);
    line-height: 22px;
    white-space: nowrap;
  }
  .contact-list .appointment { color: var(--gold-deep); }
  .contact-list svg { width: 13px; height: 13px; flex: none; }

  .address {
    position: absolute;
    right: 34px; top: 168px;
    text-align: right;
    font-size: 15px;
    line-height: 20px;
    font-style: normal;
    color: var(--text-dark);
  }
</style>
</head>
<body>

  <section class="card card--back" aria-label="Card back">
    <div class="flourish" role="img" aria-label="Faint floral swirl pattern"></div>
    <div class="brand">
      <div class="brand-name">MIRABELA COSTINA</div>
      <div class="brand-tagline">Skin Care Boutique</div>
    </div>
  </section>

  <section class="card card--front" aria-label="Card front">
    <div class="flourish" role="img" aria-label="Faint floral swirl pattern"></div>
    <div class="brand">
      <div class="brand-name">MIRABELA COSTINA</div>
      <div class="brand-tagline">Skin Care Boutique</div>
    </div>
    <div class="divider"></div>

    <div class="person">
      <div class="person-name">MIRABELA COSTINA</div>
      <div class="person-role">Esthetician</div>
      <ul class="contact-list">
        <li class="appointment">
          <svg viewBox="0 0 16 16" aria-hidden="true"><path fill="var(--gold)" d="M3 1.5l3 .5 1 3-1.6 1.2a9 9 0 0 0 4.4 4.4L11 9l3 1 .5 3-2 1.5C7 14 2 9 1.5 3.5z"/></svg>
          By appointments only: 518.240.7136
        </li>
        <li>
          <svg viewBox="0 0 16 16" aria-hidden="true"><rect x="1" y="3" width="14" height="10" fill="var(--gold)"/><path d="M1 3l7 5.5L15 3" fill="none" stroke="var(--card)" stroke-width="1.4"/></svg>
          hello@mirabelacostina.com
        </li>
        <li>
          <svg viewBox="0 0 16 16" aria-hidden="true"><circle cx="8" cy="8" r="7" fill="var(--gold)"/><path d="M1 8h14M8 1c-3 3.5-3 10.5 0 14M8 1c3 3.5 3 10.5 0 14" fill="none" stroke="var(--card)" stroke-width="1"/></svg>
          www.mirabelacostina.com
        </li>
      </ul>
    </div>

    <address class="address">
      210 Lexington Avenue<br>
      New York, NY 10016
    </address>
  </section>

</body>
</html>
```